Quillbrook IT company focused on 3 areas of IT

Looking for something similar to attached cards. Logo for quillbrook also attached.. Looking for something clean as far as colors (surprise me).. Quill stands for 3 primary areas, web design, consulting and network infrastructure design. Please email me if you have any questions. Looking forward to seeing how creative and professional this card will look. Thank you,

Target Market(s)

Small business/consumers looking for It services

Industry/Entity Type

It Service

Contact Information for Business Card

Dorin Vasek
Principal Consultant

202-555-0173

www.quillbrook-example.com
dvasek@quillbrook-example.com

27416 Copper Lantern Way,
Fernwick, OR 97999

Colors

Designer to choose colors to be used in the design.

Requirements
Must have
• attached Logo design. Feel free to play with the colors.. If you have a better idea for a card, please fee free to send me. Looking for something clean/modern. Should have tech feel, not cheesy.
Nice to have
• Surprise me :-)..

```html
<!DOCTYPE html>
<html lang="en">
<head>
<meta charset="utf-8">
<title>Quillbrook Business Card</title>
<link href="https://fonts.googleapis.com/css2?family=Lato:wght@300;400;700;900&display=swap" rel="stylesheet">
<style>
  :root {
    --ink: #1f2d2d;
    --paper: #ffffff;
    --stone: #5e5e5e;
    --muted: #8a8f8f;
    --backdrop: #e6e7e7;
  }
  * { box-sizing: border-box; margin: 0; padding: 0; }
  html, body {
    width: 1200px; height: 900px; overflow: hidden;
    background: var(--backdrop);
    font-family: "Lato", sans-serif;
  }
  .sheet {
    position: relative; width: 1200px; height: 900px;
    display: flex; flex-direction: column; align-items: center; justify-content: center; gap: 60px;
  }
  .card {
    position: relative; width: 630px; height: 360px; border-radius: 16px; overflow: hidden;
    box-shadow: 0 6px 20px rgba(0,0,0,.18);
  }

  /* Front */
  .card-front { background: var(--ink); color: var(--paper); }
  .front-brand {
    position: absolute; left: 0; right: 0; top: 128px;
    display: flex; align-items: center; justify-content: center; gap: 16px;
  }
  .brand-square { width: 30px; height: 30px; background: var(--paper); }
  .brand-name {
    font-weight: 900; font-size: 50px; letter-spacing: 2px; text-transform: uppercase; color: var(--paper);
  }
  .front-web {
    position: absolute; left: 0; right: 0; bottom: 62px; text-align: center;
    font-weight: 700; font-size: 15px; letter-spacing: 4px;
  }

  /* Back */
  .card-back { background: var(--paper); color: var(--ink); }
  .back-panel { position: absolute; inset: 0; }
  .back-brand {
    position: absolute; left: 436px; right: 0; top: 162px; text-align: center;
    font-weight: 900; font-size: 26px; letter-spacing: 1px; text-transform: uppercase; color: var(--paper);
  }
  .holder { position: absolute; left: 114px; top: 36px; }
  .holder-name { font-size: 26px; letter-spacing: 1px; text-transform: uppercase; white-space: nowrap; }
  .holder-name .first { font-weight: 900; color: var(--ink); }
  .holder-name .last { font-weight: 300; color: var(--muted); }
  .holder-title { font-size: 13px; color: var(--stone); margin-top: 2px; }

  .contact-list { position: absolute; left: 0; top: 112px; width: 400px; list-style: none; }
  .contact-row {
    position: relative; display: flex; align-items: center; height: 74px;
    border-bottom: 2px solid var(--ink);
  }
  .contact-icon {
    width: 34px; height: 34px; margin-left: 38px; background: var(--ink);
    display: flex; align-items: center; justify-content: center; flex-shrink: 0;
  }
  .contact-dot {
    position: absolute; left: 92px; bottom: -6px; width: 10px; height: 10px; border-radius: 50%; background: var(--ink);
  }
  .contact-text { margin-left: 42px; font-weight: 700; font-size: 16px; line-height: 1.35; white-space: nowrap; }
  .contact-rule { position: absolute; left: 96px; top: 100px; width: 2px; height: 240px; background: var(--ink); }
</style>
</head>
<body>
<main class="sheet">

  <section class="card card-front" aria-label="Card front">
    <div class="front-brand">
      <span class="brand-square"></span>
      <span class="brand-name">Quillbrook</span>
    </div>
    <p class="front-web">www.quillbrook-example.com</p>
  </section>

  <section class="card card-back" aria-label="Card back">
    <svg class="back-panel" width="630" height="360" viewBox="0 0 630 360">
      <polygon points="450,0 630,0 630,360 430,360 410,180" fill="var(--stone)"/>
      <polygon points="466,0 630,0 630,360 446,360 426,180" fill="var(--ink)"/>
    </svg>
    <div class="back-brand">Quillbrook</div>

    <div class="holder">
      <p class="holder-name"><span class="first">Dorin</span> <span class="last">Vasek</span></p>
      <p class="holder-title">Principal Consultant</p>
    </div>

    <span class="contact-rule"></span>
    <ul class="contact-list">
      <li class="contact-row">
        <span class="contact-icon">
          <svg width="20" height="20" viewBox="0 0 24 24" aria-hidden="true"><path fill="#fff" d="M6.6 10.8a15 15 0 0 0 6.6 6.6l2.2-2.2a1 1 0 0 1 1-.25 11.4 11.4 0 0 0 3.6.57 1 1 0 0 1 1 1V20a1 1 0 0 1-1 1A17 17 0 0 1 3 4a1 1 0 0 1 1-1h3.5a1 1 0 0 1 1 1c0 1.25.2 2.45.57 3.57a1 1 0 0 1-.25 1z"/></svg>
        </span>
        <span class="contact-dot"></span>
        <span class="contact-text">202-555-0173</span>
      </li>
      <li class="contact-row">
        <span class="contact-icon">
          <svg width="20" height="20" viewBox="0 0 24 24" aria-hidden="true"><rect x="3" y="5" width="18" height="14" fill="none" stroke="#fff" stroke-width="2"/><path d="M3 5l9 8 9-8" fill="none" stroke="#fff" stroke-width="2"/></svg>
        </span>
        <span class="contact-dot"></span>
        <span class="contact-text">dvasek@quillbrook-example.com</span>
      </li>
      <li class="contact-row">
        <span class="contact-icon">
          <svg width="20" height="20" viewBox="0 0 24 24" aria-hidden="true"><path fill="#fff" d="M12 3l9 8h-3v9h-5v-6h-2v6H6v-9H3z"/></svg>
        </span>
        <span class="contact-dot"></span>
        <span class="contact-text">27416 Copper Lantern Way,<br>Fernwick, OR 97999</span>
      </li>
    </ul>
  </section>

</main>
</body>
</html>
```